Adaptive GS Conversion & Enhancement B2B Site

We are looking to convert our current page to the adaptove Grid System (http://plinq.417.io/) and if there are some general enhancements, we would not complain :-)

We would expect delivery of static html for the following pages:
- home - http://www.bremvilo.com/
- detail - e.g. http://www.bremvilo.com/products/products.html
- help - http://www.bremvilo.com/help/te_reports/customer_approval.html

Our objective is to convert the page to a different system which is then based on the Adapt.js - from mobile.css to 2520.css

Target Market(s)

Business looking for Professional Services Project Management

Requirements
Must have
• Use of http://plinq.417.io/
Should not have
• Flash, or other frameworks (well jQuery is OK if it must be)

```html
<!DOCTYPE html>
<html lang="en">
<head>
<meta charset="utf-8">
<title>Customer Approval – Bremvilo Cloud Help</title>
<link href="https://fonts.googleapis.com/css2?family=Ubuntu:wght@300;400;500&display=swap" rel="stylesheet">
<style>
  :root{
    --orange:#f9a81a;
    --orange-edge:#f29a0c;
    --ink:#333;
    --body:#3c3c3c;
    --menu:#555;
    --muted:#666;
    --rule:#e6e6e6;
    --panel:#f7f7f7;
    --footer-bg:#f4f4f4;
    --bottom:#3a3a3a;
    --badge-blue:#1d5f8c;
    --badge-red:#e21c1c;
  }
  *{box-sizing:border-box;margin:0;padding:0}
  html,body{width:937px;height:1200px;overflow:hidden;background:#fff}
  body{font-family:"Ubuntu",sans-serif;color:var(--body)}
  .stage{width:1020px;height:1306px;transform:scale(.91863);transform-origin:0 0;position:relative;background:#fff}
  a{color:inherit;text-decoration:none}

  .site-header{position:absolute;left:0;top:0;width:1020px;height:122px;background:linear-gradient(#fff,#f6f6f6);border-top:6px solid #ececec}
  .search-tab{position:absolute;left:700px;top:0;width:244px;height:33px;background:#e9e9e9;clip-path:polygon(0 0,100% 0,93% 100%,4% 100%)}
  .search-box{position:absolute;left:721px;top:3px;width:199px;height:22px;background:#fff;border-radius:11px;font-size:11px;color:#aaa;padding:5px 12px;font-weight:300}
  .search-box svg{position:absolute;right:9px;top:4px}
  .brand{position:absolute;left:42px;top:44px;display:flex;align-items:center;gap:8px}
  .brand-dot{width:32px;height:32px;border-radius:50%;background:#3b7fc4}
  .brand-name{font-size:33px;font-weight:500;color:#222;letter-spacing:.5px}
  .main-nav{position:absolute;left:344px;top:68px;width:643px;height:47px;background:var(--orange);border-radius:4px 4px 0 0;border-bottom:1px solid var(--orange-edge);display:flex;align-items:center;padding-left:4px}
  .main-nav a{color:#fff;font-size:15px;padding:0 22px;border-left:1px solid rgba(255,255,255,.6);line-height:16px}
  .main-nav a:first-child{border-left:0}

  .help-menu{position:absolute;left:23px;top:137px;width:280px;height:873px;background:var(--panel);border:1px solid #eee;border-radius:3px}
  .help-menu .inner{position:absolute;left:6px;top:5px;right:6px;bottom:12px;background:#fff;border:1px solid #ececec;border-radius:3px}
  .help-menu ul{list-style:none;position:absolute;left:27px;top:30px;width:180px}
  .help-menu li{height:28px;font-size:13px;color:var(--menu);border-bottom:1px solid var(--rule);position:relative;line-height:28px;padding-left:19px;white-space:nowrap}
  .help-menu li:last-child{border-bottom:0}
  .help-menu li::before{content:"";position:absolute;left:6px;top:12px;border:3px solid transparent;border-left:4px solid #777}
  .help-menu li.sub{padding-left:36px}
  .help-menu li.sub::before{left:27px;border-left-color:#bbb}
  .help-menu li.sub.tight{padding-left:33px}

  .article{position:absolute;left:323px;top:156px;width:640px}
  .article h1{font-size:19px;font-weight:400;color:var(--ink);margin-bottom:11px}
  .article p{font-size:11.6px;line-height:18px;font-weight:300;color:#333;margin-bottom:28px;text-align:justify}
  .article p.close{margin-bottom:5px}
  .article .comments{font-size:12px;font-weight:500;color:#333;margin-top:36px}

  .site-footer{position:absolute;left:0;top:1027px;width:1020px;height:235px;background:var(--footer-bg)}
  .f-col{position:absolute;top:32px}
  .f-col h3{font-size:14.5px;font-weight:400;color:#333;margin-bottom:14px}
  .f-col li{list-style:none;font-size:12px;color:var(--muted);font-weight:300;line-height:25px}
  .social-icons{display:flex;gap:12px;margin:2px 0 12px}
  .social-icons span{width:26px;height:26px;background:#6d6d6d;border-radius:3px}
  .social-links{font-size:12px;color:var(--muted);font-weight:300}
  .badge-a{position:absolute;left:801px;top:34px;width:150px;height:57px;background:var(--badge-blue);border:2px solid #1a4d74;border-radius:4px}
  .badge-a::before{content:"";position:absolute;left:4px;top:4px;width:44px;height:45px;background:#fff;border-radius:3px}
  .badge-b{position:absolute;left:803px;top:100px;width:202px;height:58px;background:#fff;border:1px solid #eee}
  .badge-b::after{content:"";position:absolute;left:38px;top:32px;width:148px;height:13px;background:var(--badge-red)}
  .badge-b::before{content:"";position:absolute;left:8px;top:10px;width:150px;height:16px;background:#8a8f96;border-radius:8px;opacity:.6}

  .bottom-bar{position:absolute;left:0;top:1262px;width:1020px;height:44px;background:var(--bottom);color:#ddd;font-size:11px;font-weight:300;padding:14px 44px}
</style>
</head>
<body>
<div class="stage">
  <header class="site-header">
    <div class="search-tab"></div>
    <div class="search-box">Search here..
      <svg width="14" height="14" viewBox="0 0 14 14"><circle cx="6" cy="6" r="4.5" fill="none" stroke="#999" stroke-width="1.6"/><line x1="9.3" y1="9.3" x2="13" y2="13" stroke="#999" stroke-width="1.8"/></svg>
    </div>
    <a class="brand" href="#"><span class="brand-dot"></span><span class="brand-name">Bremvilo</span></a>
    <nav class="main-nav">
      <a href="#">Home</a><a href="#">Products</a><a href="#">Services</a><a href="#">Support</a><a href="#">Blog</a><a href="#">About Us</a><a href="#">Contact Us</a>
    </nav>
  </header>

  <aside class="help-menu">
    <div class="inner">
      <ul>
        <li>Bremvilo Cloud Help</li>
        <li class="sub tight">Welcome</li>
        <li>Opportunity Workbench</li>
        <li>Time Expense Item Workbench</li>
        <li>Workbench Setup</li>
        <li>Using Time &amp; Expense</li>
        <li class="sub tight">Time &amp; Expense Items</li>
        <li class="sub">Time &amp; Expense Reports</li>
        <li class="sub">Customer Approval</li>
        <li class="sub">Payment Selection</li>
        <li class="sub">Bremvilo Timer</li>
        <li class="sub">Dashboards &amp; Reporting</li>
        <li>Using Cloud Billing</li>
        <li class="sub">Invoices</li>
        <li>Setup: Accounting</li>
        <li class="sub">Financial Organizations</li>
        <li class="sub">Financial Accounts</li>
        <li class="sub">Taxes</li>
        <li>Setup: Time &amp; Expense</li>
        <li>Setup: Billing</li>
        <li class="sub">Document Types</li>
        <li class="sub">Payment Terms</li>
        <li>Installation</li>
        <li class="sub">Remote Sites</li>
        <li class="sub">Email Processing</li>
        <li class="sub">Security &amp; Sharing</li>
        <li class="sub">Report Approval Process</li>
        <li class="sub">Page Layouts</li>
        <li class="sub">Alerts</li>
      </ul>
    </div>
  </aside>

  <main class="article">
    <h1>CUSTOMER APPROVAL</h1>
    <p>There may be instances, generally when a customer is being billed for time and/or expenses, that it is desirable to receive a customer's approval of the time and expenses for a project or activity.&nbsp; This will help reduce the time it may take to receive payment from the customer.</p>
    <p>To use the customer approval first set up the necessary email service and ensure the Customer Approval button has been added to the T&amp;E Report page layout.&nbsp; This setup is generally done by the system administrator and details can be found in Installation.</p>
    <p>When a T&amp;E Report is in a completed status it can be submitted for customer approval.&nbsp; It is necessary to enter values in the Customer Approval section of the T&amp;E report.&nbsp; A valid Account and Contact must be entered and the contact must have a valid email address.&nbsp; This is the address the approval email is sent to.&nbsp; Select and Approval option of Time, Expense or Time &amp; Expense.&nbsp; The selection made will determine what information is included in the email text.</p>
    <p>The customer simply replies to the email with the text Approve or Reject in the first line of the response.&nbsp; Any comments can be added in the second line of the response.&nbsp; The approval status of the T&amp;E Report is updated as indicated and any comments are reflected in the Approval Comment field.&nbsp; Note that the Approval Status is separate for the Status field which is used for internal T&amp;E Report approval via the workflow.</p>
    <p class="close">If the customer rejects the T&amp;E report, modifications can be made and the T&amp;E report can be re-submitted to the customer.</p>
    <p style="margin-bottom:0">Customer approval is an optional step.&nbsp; Workflows can be designed to ensure that specific T&amp;E Reports are submitted to customers for approval provided the specific rules can be defined and replicated in the workflow environment.&nbsp; Refer to the workflow documentation in cloudvane.com or contact Bremvilo of additional assistance.</p>
    <div class="comments">Log in or register to post comments</div>
  </main>

  <footer class="site-footer">
    <div class="f-col" style="left:42px"><h3>Company</h3><ul><li>About Company</li><li>What We Do</li><li>Why We Are</li><li>Recent Blog</li><li>Services Offerd</li></ul></div>
    <div class="f-col" style="left:200px"><h3>Support</h3><ul><li>Help</li><li>FAQ</li><li>Term of Use</li><li>Support</li><li>Contact Us</li></ul></div>
    <div class="f-col" style="left:342px"><h3>Contact Information</h3><ul><li>Phone:+1 (555) 014-2290</li><li>48 Harbor Lantern Way,</li><li>Suite 410-072</li><li>Marlow Bay, CA 90017</li></ul></div>
    <div class="f-col" style="left:558px"><h3>Get In Touch</h3>
      <div class="social-icons"><span></span><span></span><span></span><span></span></div>
      <div class="social-links">Friendhub&nbsp; / &nbsp;Chirper&nbsp; / &nbsp;Viewtube&nbsp; / &nbsp;RSS</div>
    </div>
    <div class="badge-a" role="img" aria-label="Accreditation badge"></div>
    <div class="badge-b" role="img" aria-label="Platform partner badge"></div>
  </footer>
  <div class="bottom-bar">© 2012 Company Name.&nbsp; All right resreved</div>
</div>
</body>
</html>
```